New Business Card Design for Manufacturing

We are an engineering/manufacturing company that offers Advanced machining/assembly/engineering services, as well as innovative products for the heavy duty engine cooling markets.

We are looking to get a new business card designed that is clean and modern looking, but still fits the wide range of technical/skilled work we do.

- We hope to use this design as the base for other design work in new Presentations, web, and print work.

Industry/Entity Type

Engineering

Contact Information for Business Card

Our preferred color of blue is (RGB) 22/71/159 but can vary slightly from that color. Our content will be our Logo and full company name (Vantrell Forge Works, Inc.), company address, name, job title, phone number with extension, cell number, fax number, website, and email address on the cards.
We'd like the full company name next to the logo, but we are open to other interpretations of that layout.
Preferably, we would like the back side to be clean with just our logo, and the front to contain all of the contact information.

Colors
2f74b4
0355a3
85abd2

Requirements
Must have
• - Logo, company name, needed content - We are open to interpretation beyond that.
• - Standard size business card.
• - Horizontal orientation.
• - Enough space for lengthy names / job titles (for example, a job title could read "Directory of Human Resources" or "V.P. of Governmental Affairs"). We need this to look clean, whether the title be short (CEO) or long (as described above).

```html
<!DOCTYPE html>
<html lang="en">
<head>
<meta charset="utf-8">
<title>Vantrell Forge Works — Business Card</title>
<link href="https://fonts.googleapis.com/css2?family=Montserrat:wght@400;500;700;800&display=swap" rel="stylesheet">
<style>
  :root {
    --brand-blue: #1459ad;
    --brand-deep: #0f4c9a;
    --brand-light: #85abd2;
    --ink: #4a4d52;
    --rule: #9a9da2;
    --tab-grey: #a7aaae;
    --paper: #ffffff;
    --stage: #e9eaec;
  }
  * { box-sizing: border-box; margin: 0; padding: 0; }
  html, body {
    width: 1200px; height: 716px; overflow: hidden;
    background: var(--stage);
    font-family: "Montserrat", Arial, sans-serif;
  }
  .stage { position: relative; width: 1200px; height: 716px; }

  .card {
    position: absolute; top: 210px;
    width: 520px; height: 297px;
    border-radius: 4px; overflow: hidden;
    box-shadow: 0 6px 18px rgba(0,0,0,.18);
  }

  /* Back side */
  .card-back { left: 60px; background: var(--brand-blue); }
  .card-back .world-map {
    position: absolute; left: 70px; top: 30px; width: 380px; height: 190px;
    background: radial-gradient(ellipse at center, rgba(255,255,255,.10), rgba(255,255,255,0) 70%);
  }
  .card-back .wordmark {
    position: absolute; left: 0; right: 0; top: 118px; text-align: center;
    color: #fff; font-weight: 800; font-size: 32px; letter-spacing: .5px;
  }
  .card-back .website {
    position: absolute; left: 40px; bottom: 34px;
    color: #fff; font-size: 11px; font-weight: 500;
  }

  /* Front side */
  .card-front { left: 620px; background: var(--paper); }
  .card-front .wordmark {
    position: absolute; right: 30px; top: 58px;
    color: var(--brand-blue); font-weight: 800; font-size: 24px;
  }
  .card-front .person { position: absolute; left: 28px; top: 86px; }
  .card-front .person-name { color: var(--brand-blue); font-size: 17px; font-weight: 700; }
  .card-front .person-title { color: var(--ink); font-size: 10px; margin-top: 3px; }
  .card-front .rule-top {
    position: absolute; left: 28px; right: 30px; top: 128px;
    border-top: 1px solid var(--rule);
  }
  .card-front .contact-list { position: absolute; left: 28px; top: 138px; list-style: none; }
  .card-front .contact-list li {
    display: flex; align-items: center; gap: 7px;
    color: var(--ink); font-size: 10.5px; line-height: 17px;
  }
  .card-front .contact-list svg { width: 10px; height: 10px; fill: var(--brand-blue); }
  .card-front .website {
    position: absolute; left: 28px; top: 214px;
    color: var(--brand-blue); font-size: 11px; font-weight: 500;
  }
  .card-front .rule-address {
    position: absolute; left: 260px; right: 30px; top: 200px;
    border-top: 1px solid var(--rule);
  }
  .card-front .address {
    position: absolute; right: 30px; top: 212px; text-align: right;
    color: var(--ink); font-size: 10.5px; line-height: 16px;
  }
  .card-front .band-grey {
    position: absolute; left: 140px; right: 0; bottom: 10px; height: 16px;
    background: var(--tab-grey); border-top-left-radius: 8px;
  }
  .card-front .band-blue {
    position: absolute; left: 0; right: 0; bottom: 0; height: 10px;
    background: var(--brand-blue);
  }
  .card-front .band-blue-tab {
    position: absolute; left: 0; width: 140px; bottom: 10px; height: 16px;
    background: var(--brand-blue);
  }
</style>
</head>
<body>
<main class="stage">

  <section class="card card-back" aria-label="Business card back">
    <div class="world-map" role="img" aria-label="Faint world map backdrop"></div>
    <div class="wordmark">Vantrell Forge Works</div>
    <div class="website">www.yourmailaddress.com</div>
  </section>

  <section class="card card-front" aria-label="Business card front">
    <div class="wordmark">Vantrell Forge Works</div>

    <div class="person">
      <div class="person-name">Marcus Hale</div>
      <div class="person-title">President</div>
    </div>
    <div class="rule-top"></div>

    <ul class="contact-list">
      <li><svg viewBox="0 0 10 10" aria-hidden="true"><path d="M2 0.5 L3.8 2.6 L2.8 3.8 Q4 6.2 6.2 7.2 L7.4 6.2 L9.5 8 L8.2 9.5 Q2.5 9 0.5 2 Z"/></svg>+000.000.00 00</li>
      <li><svg viewBox="0 0 10 10" aria-hidden="true"><path d="M3 0 H7 Q8 0 8 1 V9 Q8 10 7 10 H3 Q2 10 2 9 V1 Q2 0 3 0 Z M3 1.5 V7.5 H7 V1.5 Z"/></svg>+000.000.00 00</li>
      <li><svg viewBox="0 0 10 10" aria-hidden="true"><path d="M2.5 0 H7.5 V3 H2.5 Z M0 3.5 H10 V8 H8 V10 H2 V8 H0 Z M3 7 V9 H7 V7 Z"/></svg>+000.000.00 00</li>
      <li><svg viewBox="0 0 10 10" aria-hidden="true"><path d="M0 2 H10 V8.5 H0 Z M0.8 2.6 L5 5.8 L9.2 2.6 V3.6 L5 6.8 L0.8 3.6 Z" fill-rule="evenodd"/></svg>+000.000.00 00</li>
    </ul>
    <div class="website">www.yourmailaddress.com</div>

    <div class="rule-address"></div>
    <div class="address">Street Name Avenue, Suite 100<br>State, Zip Code, Country</div>

    <div class="band-grey"></div>
    <div class="band-blue-tab"></div>
    <div class="band-blue"></div>
  </section>

</main>
</body>
</html>
```